Harbor Ledger Funds Bus card and Logo

I need a logo design and Bus card design. The fund focuses on evaluating and investing in minerals (sub-surface rights) and real estate.

Harbor ledger refers to a book of knowledge that each plebe gets when entering the Kelmont Marine Academy (my alma mater)

Target Market(s)

Investors and financial advisors

Contact Information for Business Card

Simple - perhaps a logo with a theme on book of knowledge

Logo Text

Ex Scientia Imperium

Font styles to use
Serif
Sans Serif

Colors

Designer to choose colors to be used in the design.

Requirements
Must have
• memorable logo that is relatively simple

```html
<!DOCTYPE html>
<html lang="en">
<head>
<meta charset="utf-8">
<title>Harbor Ledger Funds – Business Card</title>
<link href="https://fonts.googleapis.com/css2?family=Lato:wght@400;700&family=Roboto:wght@400;500&display=swap" rel="stylesheet">
<style>
  :root {
    --backdrop: #a3a3a3;
    --card-front: #ffffff;
    --card-back: #2a2a2a;
    --pattern-tone: #313131;
    --ink: #2f2f2f;
    --accent-blue: #2b93d1;
    --divider: #d6dde3;
    --rule-front: #9a9a9a;
    --back-text: #dcdcdc;
    --rule-back: #8a8a8a;
  }
  * { margin: 0; padding: 0; box-sizing: border-box; }
  html, body { width: 1200px; height: 802px; overflow: hidden; }
  body { background: var(--backdrop); position: relative; font-family: "Lato", sans-serif; }

  .card {
    position: absolute; top: 274px; width: 443px; height: 264px;
    box-shadow: 0 3px 8px rgba(0,0,0,0.35);
  }
  .card-front { left: 136px; background: var(--card-front); }
  .card-back { left: 624px; background: var(--card-back); overflow: hidden; }

  /* Wordmark: one colour, one weight */
  .wordmark {
    font-family: "Roboto", sans-serif; font-weight: 500;
    text-align: center; white-space: nowrap;
  }
  .wordmark-name { display: block; font-size: 24px; line-height: 28px; letter-spacing: 0.2px; }
  .wordmark-line { display: flex; align-items: center; gap: 6px; margin-top: 2px; }
  .wordmark-line .rule { flex: 1; height: 1px; }
  .wordmark-sub { font-size: 10.5px; line-height: 12px; letter-spacing: 7px; margin-right: -7px; }

  .brand-block { position: absolute; left: 22px; top: 70px; width: 200px; }
  .brand-dot { display: block; width: 70px; height: 70px; border-radius: 50%; background: var(--accent-blue); margin: 0 auto 22px; }
  .brand-block .wordmark { color: var(--ink); }
  .brand-block .rule { background: var(--rule-front); }

  .divider { position: absolute; left: 229px; top: 69px; width: 1px; height: 132px; background: var(--divider); }

  .contact { position: absolute; left: 247px; top: 64px; color: var(--ink); }
  .person-name { font-family: "Roboto", sans-serif; font-weight: 500; color: var(--accent-blue); font-size: 18.5px; line-height: 22px; }
  .person-role { font-size: 13px; line-height: 15px; margin-bottom: 6px; }
  .contact-list { list-style: none; }
  .contact-list li { display: flex; align-items: center; gap: 4px; font-size: 12.5px; line-height: 16px; }
  .contact-list svg { width: 9px; height: 9px; fill: var(--accent-blue); flex: none; }
  .address { font-size: 12.5px; line-height: 15.5px; margin-top: 6px; }

  .back-pattern {
    position: absolute; inset: 0;
    background: linear-gradient(180deg, var(--pattern-tone), var(--card-back));
  }
  .back-brand { position: absolute; left: 122px; top: 108px; width: 200px; }
  .back-brand .wordmark { color: var(--back-text); }
  .back-brand .rule { background: var(--rule-back); }
</style>
</head>
<body>
  <section class="card card-front">
    <div class="brand-block">
      <span class="brand-dot"></span>
      <p class="wordmark">
        <span class="wordmark-name">HARBOR LEDGER</span>
        <span class="wordmark-line"><span class="rule"></span><span class="wordmark-sub">FUNDS</span><span class="rule"></span></span>
      </p>
    </div>
    <div class="divider"></div>
    <div class="contact">
      <h1 class="person-name">DANIEL HARTWELL</h1>
      <p class="person-role">Managing Director</p>
      <ul class="contact-list">
        <li><svg viewBox="0 0 10 10"><path d="M1 3c0-1 1-2 4-2s4 1 4 2v1H7V3H3v1H1zM2 5h6l1 4H1z"/></svg>044-123 456 789</li>
        <li><svg viewBox="0 0 10 10"><path d="M3 0h4a1 1 0 0 1 1 1v8a1 1 0 0 1-1 1H3a1 1 0 0 1-1-1V1a1 1 0 0 1 1-1zm0 1.5v6h4v-6z"/></svg>044-123 456 789</li>
        <li><svg viewBox="0 0 10 10"><path d="M0 2h10v6H0zM1 3l4 3 4-3v-.5H1z" fill-rule="evenodd"/></svg>info@harborledgerfunds.com</li>
        <li><svg viewBox="0 0 10 10"><circle cx="5" cy="5" r="4.5"/></svg>www.harborledgerfunds.com</li>
      </ul>
      <p class="address">12345, Address Goes Here<br>Country Name, 123456.</p>
    </div>
  </section>

  <section class="card card-back">
    <div class="back-pattern" role="img" aria-label="Faint repeating brand-mark pattern across the dark card back"></div>
    <div class="back-brand">
      <p class="wordmark">
        <span class="wordmark-name">HARBOR LEDGER</span>
        <span class="wordmark-line"><span class="rule"></span><span class="wordmark-sub">FUNDS</span><span class="rule"></span></span>
      </p>
    </div>
  </section>
</body>
</html>
```